Women's health flyer for Vindbro Health & Wellness . for a Women's health conference

I need a flyer , post card 4x 6 or 5 x 7 sized designed , 2 sides focused on my business branding and Women's health. we deliver bespoke care and focus on all phases of women's health and life. I want something aligned with our bespoke whole person care philosophy and that is fresh and forward thinking.
www.vindbro-care.com
This is to help women know they can have care for all phases of life , fertility , postpartum , perimenopause , mental health , wellness, weight loss, increased energy stress , menopause etc
please use knowledge from website about my company , www.vindbro-care.com
I also feel like my brand kit could use an additional secondarily color option in it

Target Market(s)

Women 25-70

Industry/Entity Type

health & Wellness

Colors
0054AA
0677BA
7BADD7
CADEEF
E8F1F8
0094D4
00A9DD
6FCCEA
C7EBF8
E9F6FB
00AB8E
00BBA5
67D7C9
C6EFE9
E9F9F6
59FF00
82FF00
B8FF75
E3FFCB
F4FFEA
E54698
E96AAD
F1A4CE
F9D9EA
FCEFF6
A7469A
B969AE
D3A5CF
EDDBEB
F8F0F9

Requirements
Must have
• photos , my logo, connection to my brand
Nice to have
• something fresh and different
Should not have
• look like a genetic "wellness program"

```html
<!DOCTYPE html>
<html lang="en">
<head>
<meta charset="utf-8">
<title>Vindbro Health &amp; Wellness – Postcard</title>
<link rel="stylesheet" href="https://fonts.googleapis.com/css2?family=Dancing+Script:wght@500&family=Marcellus&family=Montserrat:wght@500;600;700&display=swap">
<style>
  :root{
    --canvas:#c6def3;
    --teal-light:#2fd8e8;
    --teal:#1aa3cf;
    --teal-deep:#0a6f98;
    --navy:#0c4f88;
    --purple:#a04a98;
    --purple-deep:#6d2e6b;
    --green:#6cb32a;
    --green-bright:#7fc43a;
    --mint:#3ccfc0;
    --pill-teal:#12a58a;
    --pill-pink:#c266b5;
    --pill-blue:#1fa9e0;
    --pill-mint:#4fcfb8;
    --white:#ffffff;
    --serif:'Marcellus', serif;
    --script:'Dancing Script', cursive;
    --sans:'Montserrat', sans-serif;
  }
  *{box-sizing:border-box;margin:0;padding:0}
  html,body{width:1200px;height:1200px;overflow:hidden;background:var(--canvas)}
  .stage{position:relative;width:1200px;height:1200px}
  .card{position:absolute;left:233px;width:734px;height:489px;overflow:hidden;background:var(--white);box-shadow:0 8px 22px rgba(30,60,100,.28)}
  .card--front{top:86px}
  .card--back{top:638px}
  .card svg.shapes{position:absolute;inset:0;width:734px;height:489px}
  .abs{position:absolute}

  /* front */
  .photo-beach{position:absolute;left:0;top:0;width:734px;height:489px;
    background:linear-gradient(180deg,#a9d4ef 0%,#9fcfee 15%,#1fb6e0 18%,#3bc4e6 45%,#e9f3f6 62%,#d6c5a8 74%,#a08765 100%)}
  .title-script{left:42px;top:17px;font-family:var(--script);font-size:108px;line-height:1;color:var(--white);white-space:nowrap}
  .title-serif{left:43px;top:116px;font-family:var(--serif);font-size:42px;line-height:44px;color:var(--white);white-space:nowrap}
  .title-rule{left:43px;top:163px;width:385px;height:1px;background:#7fe3f2}
  .title-caps{left:43px;top:168px;font-family:var(--serif);font-size:39px;line-height:35px;color:var(--white);white-space:nowrap}
  .pill{position:absolute;height:21px;border-radius:5px;font-family:var(--serif);font-size:13px;line-height:21px;color:var(--white);padding:0 9px;white-space:nowrap}
  .pill--green{background:var(--green)}
  .pill--teal{background:var(--pill-teal)}
  .pill--pink{background:var(--pill-pink)}
  .pill--blue{background:var(--pill-blue)}
  .pill--mint{background:var(--pill-mint)}
  .brand{text-align:center;font-family:var(--serif);color:var(--navy)}
  .brand__name{display:block;letter-spacing:.5px}
  .brand__sub{display:block;letter-spacing:2.5px}
  .front-brand{left:20px;top:420px;width:180px}
  .front-brand .brand__name{font-size:31px;line-height:32px}
  .front-brand .brand__sub{font-size:7.5px}
  .phases-bar{left:239px;top:386px;width:260px;height:17px;background:linear-gradient(90deg,var(--green-bright),rgba(127,196,58,.35));font-family:var(--sans);font-weight:700;font-size:9.5px;letter-spacing:.6px;line-height:17px;color:var(--white);padding-left:6px;white-space:nowrap}
  .phases{list-style:none;font-family:var(--serif);font-size:11px;line-height:12.8px;color:var(--white);white-space:nowrap}
  .phases li::before{content:"";display:inline-block;width:5px;height:5px;border:1px solid var(--white);border-radius:50%;margin-right:5px;vertical-align:1px}
  .phases--a{left:240px;top:412px}
  .phases--b{left:349px;top:413px}
  .call{font-family:var(--serif);color:var(--white);white-space:nowrap}
  .call__label{display:block;font-size:17px;line-height:18px}
  .call__phone{display:block;font-family:var(--sans);font-weight:700;font-size:16px;line-height:19px;letter-spacing:.3px}
  .front-call{left:573px;top:405px}
  .url-pill{position:absolute;height:18px;border-radius:9px;background:var(--mint);font-family:var(--sans);font-weight:600;font-size:9.5px;letter-spacing:1px;line-height:18px;color:var(--white);text-align:center;white-space:nowrap}
  .front-url{left:564px;top:444px;width:152px}

  /* back */
  .back-brand{left:33px;top:69px;width:102px}
  .back-brand .brand__name{font-size:18px;line-height:18px}
  .back-brand .brand__sub{font-size:4.5px;letter-spacing:1.3px}
  .headline{left:155px;top:32px;font-family:var(--serif);font-size:30px;line-height:30px;color:var(--white);white-space:nowrap}
  .rule{position:absolute;left:155px;width:236px;height:1px;background:#62dcef}
  .why{left:43px;top:156px;width:152px;height:23px;border-radius:12px;background:var(--green);font-family:var(--serif);font-size:16px;line-height:23px;color:var(--white);text-align:center}
  .feature-icon{position:absolute;width:33px;height:33px;border-radius:50%;background:var(--white);box-shadow:0 0 0 2px rgba(255,255,255,.4)}
  .feature-icon svg{width:33px;height:33px}
  .feature-label{position:absolute;font-family:var(--sans);font-weight:700;font-size:9.5px;line-height:9px;color:var(--white);letter-spacing:.4px;white-space:nowrap}
  .photo-round{position:absolute;border-radius:50%}
  .photo-meditate{left:175px;top:184px;width:106px;height:106px;background:radial-gradient(circle at 50% 55%,#7fa6d6 0%,#c8ccd3 45%,#e9ebee 100%);border:2px solid var(--white)}
  .photo-portrait{left:33px;top:295px;width:96px;height:96px;background:radial-gradient(circle at 55% 45%,#cfcfcf 0%,#7a7a7a 55%,#2a2a2a 100%);border:3px solid #d9c8b4}
  .doctor{left:155px;top:313px;font-family:var(--sans);font-weight:700;font-size:10.5px;letter-spacing:.5px;color:var(--white);white-space:nowrap}
  .bio{left:155px;top:331px;width:260px;font-family:var(--sans);font-weight:500;font-size:6.6px;line-height:9.3px;color:var(--white)}
  .back-call{left:36px;top:428px}
  .back-url{left:180px;top:446px;width:152px}
</style>
</head>
<body>
<main class="stage">

  <section class="card card--front" aria-label="Postcard front">
    <div class="photo-beach" role="img" aria-label="Photo of a woman in a white dress walking barefoot on the beach toward the sea, holding a straw hat"></div>
    <svg class="shapes" viewBox="0 0 734 489" aria-hidden="true">
      <defs>
        <radialGradient id="frontTeal" cx="0.3" cy="0.05" r="0.9">
          <stop offset="0" stop-color="#2fdbe9"/>
          <stop offset="0.5" stop-color="#18a4cd"/>
          <stop offset="1" stop-color="#0a6b94"/>
        </radialGradient>
        <linearGradient id="frontPurple" x1="0" y1="0" x2="0" y2="1">
          <stop offset="0" stop-color="#b463ab"/>
          <stop offset="1" stop-color="#6d2e6b"/>
        </linearGradient>
      </defs>
      <path d="M0 0 H492 Q470 300 200 382 L0 400 Z" fill="url(#frontTeal)" stroke="#0a5f86" stroke-width="2"/>
      <path d="M494 489 Q520 368 734 364 V489 Z" fill="url(#frontPurple)" stroke="#c98ac2" stroke-width="2"/>
      <circle cx="106" cy="438" r="112" fill="#ffffff" stroke="#cfd6dc" stroke-width="3"/>
    </svg>

    <div class="abs title-script">Women's</div>
    <div class="abs title-serif">Health and Wellness</div>
    <div class="abs title-rule"></div>
    <div class="abs title-caps">PERSONAL WHOLE<br>BESPOKE CARE</div>

    <span class="pill pill--green" style="left:49px;top:253px">Retreats</span>
    <span class="pill pill--teal" style="left:128px;top:253px">Workshops</span>
    <span class="pill pill--pink" style="left:221px;top:253px">Individual Coaching</span>
    <span class="pill pill--blue" style="left:49px;top:283px">Acupuncture</span>
    <span class="pill pill--mint" style="left:157px;top:283px">Corporate Wellness</span>

    <div class="abs brand front-brand">
      <span class="brand__name">VINDBRO</span>
      <span class="brand__sub">HEALTH &amp; WELLNESS</span>
    </div>

    <div class="abs phases-bar">WE HELP YOU IN ALL PHASES OF YOUR LIFE:</div>
    <ul class="abs phases phases--a">
      <li>Fertility</li><li>Postpartum</li><li>Perimenopause</li><li>Mental Health</li>
    </ul>
    <ul class="abs phases phases--b">
      <li>Wellness</li><li>Weight Loss</li><li>Increased Energy Stress</li><li>Menopause</li>
    </ul>

    <div class="abs call front-call">
      <span class="call__label">CALL US TODAY</span>
      <span class="call__phone">1-555-014-2290</span>
    </div>
    <div class="url-pill front-url">www.vindbro-care.com</div>
  </section>

  <section class="card card--back" aria-label="Postcard back">
    <svg class="shapes" viewBox="0 0 734 489" aria-hidden="true">
      <defs>
        <radialGradient id="backTeal" cx="0.2" cy="0.1" r="1">
          <stop offset="0" stop-color="#2fdbe9"/>
          <stop offset="0.55" stop-color="#18a0cb"/>
          <stop offset="1" stop-color="#0a6b94"/>
        </radialGradient>
        <linearGradient id="backPurple" x1="0" y1="0" x2="0" y2="1">
          <stop offset="0" stop-color="#b463ab"/>
          <stop offset="1" stop-color="#6d2e6b"/>
        </linearGradient>
      </defs>
      <path d="M0 0 H376 Q520 245 400 489 H0 Z" fill="url(#backTeal)" stroke="#0a5f86" stroke-width="2"/>
      <path d="M0 408 Q250 392 409 489 H0 Z" fill="url(#backPurple)" stroke="#c98ac2" stroke-width="2"/>
      <circle cx="85" cy="82" r="57" fill="#ffffff" stroke="#cfd6dc" stroke-width="3"/>
    </svg>

    <div class="abs brand back-brand">
      <span class="brand__name">VINDBRO</span>
      <span class="brand__sub">HEALTH &amp; WELLNESS</span>
    </div>

    <div class="abs headline">JOIN US IN THIS<br>REVOLUTION OF<br>WELLBEING</div>
    <div class="rule" style="top:131px"></div>

    <div class="abs why">WHY CHOOSE US</div>

    <div class="feature-icon" style="left:34px;top:198px">
      <svg viewBox="0 0 33 33" aria-hidden="true"><path d="M16.5 23 C10 18 9 14.5 11.5 12.5 C13.5 11 15.5 12 16.5 13.6 C17.5 12 19.5 11 21.5 12.5 C24 14.5 23 18 16.5 23 Z" fill="none" stroke="#6cb32a" stroke-width="1.4"/></svg>
    </div>
    <div class="feature-label" style="left:74px;top:205px">WHOLE<br>PERSON<br>APPROACH</div>

    <div class="feature-icon" style="left:34px;top:244px">
      <svg viewBox="0 0 33 33" aria-hidden="true"><path d="M16.5 10 C13.5 14 13.5 18 16.5 22 C19.5 18 19.5 14 16.5 10 Z M16.5 22 C12 21 9.5 18 9 15 C12 15 14.5 17 16.5 22 Z M16.5 22 C21 21 23.5 18 24 15 C21 15 18.5 17 16.5 22 Z" fill="none" stroke="#6cb32a" stroke-width="1.3"/></svg>
    </div>
    <div class="feature-label" style="left:71px;top:256px">COMPREHENSIVE<br>SUPPORT:</div>

    <div class="photo-round photo-meditate" role="img" aria-label="Photo of a woman meditating cross-legged in a bright room"></div>

    <div class="feature-icon" style="left:289px;top:200px">
      <svg viewBox="0 0 33 33" aria-hidden="true"><circle cx="16.5" cy="15" r="6.5" fill="none" stroke="#6cb32a" stroke-width="1.4"/><path d="M13 21 L13 25 L20 25 L20 21" fill="none" stroke="#6cb32a" stroke-width="1.4"/></svg>
    </div>
    <div class="feature-label" style="left:335px;top:207px">REVOLUTIONARY<br>DESIGNED<br>PROGRAMS</div>

    <div class="feature-icon" style="left:289px;top:246px">
      <svg viewBox="0 0 33 33" aria-hidden="true"><path d="M16.5 8 L18.6 14 L25 14.2 L20 18 L21.8 24.2 L16.5 20.5 L11.2 24.2 L13 18 L8 14.2 L14.4 14 Z" fill="none" stroke="#6cb32a" stroke-width="1.3"/></svg>
    </div>
    <div class="feature-label" style="left:335px;top:257px">COMMUNITY &amp;<br>INDIVIDUALITY</div>

    <div class="rule" style="top:303px"></div>

    <div class="photo-round photo-portrait" role="img" aria-label="Black and white portrait photo of the practitioner"></div>
    <div class="abs doctor">DR MAREN L OSTVIK DACM, L.AC.</div>
    <p class="abs bio">From a young age, Traditional East Asian Medicine (T.E.A.M) played a pivotal role in overcoming significant lung concerns, allowing me to pursue my aspirations as a young athlete. This early encounter sparked a lifelong dedication to healing and prompted a deep exploration of how best to serve and empower my community. The answer crystallized: Traditional East Asian Medicine.</p>

    <div class="abs call back-call">
      <span class="call__label">CALL US TODAY</span>
      <span class="call__phone">1-555-014-2290</span>
    </div>
    <div class="url-pill back-url">www.vindbro-care.com</div>
  </section>

</main>
</body>
</html>
```